Report template for evaluation reports to be used by non designers

We are looking for a report template that meets all the requirements listed in the attached documents. letter head, logo etc have been enclosed. Its important that the colour integrity is kept, but beyond that options are welcome.
Its important that the document is extremely easy to use and that is able to be adapted to include eatables, figures, pictures, text boxes etc and keep the integrity of the template

Target Market(s)

Governments, Civil society organisations and research institutions

Font styles to use
Sans Serif

Colors
6b449b
876aae
c0c0c0
000000

Requirements
Must have
• Clean, professional, not concluded, modern, must be easy to use
Should not have
• too busy, hard to use

```html
<!DOCTYPE html>
<html lang="en">
<head>
<meta charset="utf-8">
<title>Meridian Research Institute – 2018 Annual Report</title>
<link rel="stylesheet" href="https://fonts.googleapis.com/css2?family=Open+Sans:ital,wght@0,300;0,400;0,700;1,400&display=swap">
<style>
  :root {
    --purple: #6b449b;
    --purple-soft: #876aae;
    --purple-band: #5e4a9b;
    --silver: #c0c0c0;
    --ink: #1a1a1a;
    --paper: #ffffff;
    --backdrop: #dcdcdc;
    --body-grey: #9a9a9a;
  }
  * { margin: 0; padding: 0; box-sizing: border-box; }
  html, body {
    width: 1200px;
    height: 784px;
    overflow: hidden;
    background: var(--backdrop);
  }
  .stage {
    width: 1200px;
    height: 784px;
    display: flex;
    align-items: center;
    justify-content: center;
  }
  .report-cover {
    width: 500px;
    height: 708px;
    display: block;
    box-shadow: 0 10px 28px rgba(0,0,0,0.18);
    font-family: "Open Sans", Arial, sans-serif;
  }
  .page { fill: var(--paper); }
  .band { fill: var(--purple-band); }
  .band-dark { fill: var(--purple); }
  .panel { fill: var(--paper); }
  .ribbon { fill: var(--purple-soft); opacity: 0.82; }
  .intro-heading {
    font-family: "Open Sans", Arial, sans-serif;
    font-weight: 700;
    font-size: 8.5px;
    fill: var(--purple);
    letter-spacing: 0.2px;
  }
  .intro-marker { fill: var(--purple); }
  .intro-body {
    font-family: "Open Sans", Arial, sans-serif;
    font-style: italic;
    font-size: 7px;
    fill: var(--body-grey);
  }
  .cover-year {
    font-family: "Open Sans", Arial, sans-serif;
    font-weight: 700;
    font-size: 58px;
    fill: var(--paper);
    letter-spacing: 3px;
  }
  .cover-title {
    font-family: "Open Sans", Arial, sans-serif;
    font-weight: 700;
    font-size: 22px;
    fill: var(--paper);
    letter-spacing: 0.5px;
  }
  .org-name {
    font-family: "Open Sans", Arial, sans-serif;
    font-weight: 300;
    font-size: 46px;
    fill: var(--ink);
    letter-spacing: 7px;
  }
  .org-sub {
    font-family: "Open Sans", Arial, sans-serif;
    font-weight: 300;
    font-size: 10.5px;
    fill: var(--ink);
    letter-spacing: 5px;
  }
</style>
</head>
<body>
<main class="stage">
  <svg class="report-cover" viewBox="0 0 480 680" xmlns="http://www.w3.org/2000/svg">
    <defs>
      <linearGradient id="photo-tone" x1="0" y1="0" x2="1" y2="1">
        <stop offset="0" stop-color="#5a5a5a"/>
        <stop offset="0.45" stop-color="#a8a8a8"/>
        <stop offset="0.75" stop-color="#d6d6d6"/>
        <stop offset="1" stop-color="#3a3a3a"/>
      </linearGradient>
    </defs>

    <rect class="page" x="0" y="0" width="480" height="680"/>

    <!-- top band -->
    <rect class="band" x="0" y="0" width="480" height="20"/>

    <!-- introduction block -->
    <g class="intro">
      <polygon class="intro-marker" points="40,42 40,50 47,46"/>
      <text class="intro-heading" x="51" y="49">LOREM IPSUM DOLOR SIT AMET</text>
      <text class="intro-body">
        <tspan x="40" y="66">Our evaluation work brings evidence to public</tspan>
        <tspan x="40" y="76">decisions. This report sets out the year in</tspan>
        <tspan x="40" y="86">review, key findings from our programmes,</tspan>
        <tspan x="40" y="96">and the partners who made the research</tspan>
        <tspan x="40" y="106">possible across the region.</tspan>
      </text>
    </g>

    <!-- cover photograph area -->
    <polygon class="cover-photo" role="img"
      aria-label="Black and white photograph of a busy city street with traffic and overhead tram wires"
      fill="url(#photo-tone)"
      points="0,140 250,140 480,300 480,480 0,480"/>

    <!-- title ribbon -->
    <polygon class="ribbon" points="0,172 330,172 372,228 330,284 0,284"/>
    <text class="cover-year" x="40" y="236">2018</text>
    <text class="cover-title" x="40" y="268">ANNUAL REPORT</text>

    <!-- purple diagonal band -->
    <polygon class="band" points="0,320 450,500 0,500"/>
    <polygon class="band-dark" points="0,340 400,500 0,500" opacity="0.35"/>

    <!-- white logo panel -->
    <polygon class="panel" points="70,390 110,375 480,520 480,680 40,680 40,420"/>

    <!-- left and bottom edge strips -->
    <rect class="band" x="0" y="480" width="40" height="200"/>
    <rect class="band" x="0" y="664" width="480" height="16"/>

    <!-- organisation name -->
    <g class="org-identity">
      <text class="org-name" x="92" y="548">MERIDIAN</text>
      <text class="org-sub" x="96" y="572">RESEARCH INSTITUTE</text>
    </g>
  </svg>
</main>
</body>
</html>
```